Wordpress Design Project for Bankruptcy Law Office in San Francisco

our current website: www.dorvanelilaw-example.com

we would like to re-design it for wordpress to make it faster and a bit more modern.

content should be similar to what we have there right now but also we do family law

please include logo for law office:

Law Office of Marta K. Dolvenidze

Thank you.
Updates

please see attached word document with logos that we like as an example.

we do tend to like color red.  darker red.

Please submit your design variations and logo as soon as possible.   We would like to go over them and make our decision

Reason: Please create couple of more variations of logo for your design, so we can make our decision what we like the most. Please see word doc for samples: Text: Law Office Of Marta K. Dolvenidze

Reason: final touches

Target Market(s)

bankruptcy and family law clients

Industry/Entity Type

Family Law

Requirements
Must have
• see examples of law sites
http://promo.lexorbin-example.com/testimonials

- new logo: Law Office of Marta K. Dolvenidze
- client intake form
- blog
- contact us form

Nice to have
• - map
- red color
- on the front page a nice photo of SF or a happy family

```html
<!DOCTYPE html>
<html lang="en">
<head>
<meta charset="utf-8">
<title>Law Office of Marta K. Dolvenidze</title>
<link rel="stylesheet" href="https://fonts.googleapis.com/css2?family=Cinzel:wght@400&family=Roboto+Condensed:wght@500&family=PT+Sans:wght@400;700&family=Amatic+SC:wght@700&family=Arimo:wght@400;700&display=swap">
<style>
:root{
  --page-bg:#dcdcdc;
  --red-dark:#7a0710;
  --red:#b10d1c;
  --green:#3f8a2c;
  --green-dark:#1d5a16;
  --ink:#222;
  --body:#3a3a3a;
  --white:#fff;
}
*{box-sizing:border-box;margin:0;padding:0}
html,body{width:1011px;height:1200px;overflow:hidden;background:var(--page-bg)}
.canvas{position:relative;width:1011px;height:1200px;overflow:hidden;background:var(--page-bg);font-family:"PT Sans",sans-serif;color:var(--body)}
.page{position:absolute;left:97px;top:17px;width:817px;height:1160px;background:var(--white);box-shadow:0 0 14px rgba(0,0,0,.35)}
.header{position:absolute;left:97px;top:17px;width:817px;height:91px;background:linear-gradient(180deg,#c01222 0%,#a10b18 55%,var(--red-dark) 100%)}
.brand{position:absolute;left:20px;top:14px;display:flex;align-items:flex-start;gap:10px;font-family:"Cinzel",serif;color:var(--white)}
.brand-mark{width:24px;height:24px;background:var(--white);margin-top:4px}
.brand-name{font-size:20px;line-height:24px;letter-spacing:.5px}
.brand-name small{display:block;font-size:20px}
.phone{position:absolute;right:10px;top:50px;display:flex;align-items:center;gap:8px;font-family:"Cinzel",serif;font-size:22px;color:var(--white)}
.phone svg{width:22px;height:22px}
.nav{position:absolute;left:80px;top:108px;width:851px;height:37px;background:var(--green);display:flex;padding-left:35px;box-shadow:0 2px 3px rgba(0,0,0,.3)}
.nav a{font-family:"Roboto Condensed",sans-serif;font-size:17px;color:var(--white);text-decoration:none;line-height:37px;padding:0 19px;white-space:nowrap}
.nav a.current{background:var(--green-dark);padding:0 20px;width:87px}
.nav-fold{position:absolute;top:145px;width:0;height:0;border-top:14px solid #111}
.nav-fold.left{left:80px;border-left:17px solid transparent}
.nav-fold.right{left:914px;border-right:17px solid transparent}
.hero{position:absolute;left:114px;top:166px;width:786px;height:325px;background:linear-gradient(180deg,#1f3a14 0%,#3d6a22 40%,#8c9e62 62%,#c9b56f 72%,#4d6a2a 85%,#2a4a18 100%)}
.hero-line{position:absolute;left:503px;top:116px;font-family:"Amatic SC",sans-serif;font-size:34px;line-height:36px;color:#1a1a12;text-align:center;width:230px}
.intake{position:absolute;left:114px;top:497px;width:202px;height:295px;background:var(--green);border:1px dotted #555;padding:10px 12px}
.intake h3{font-size:15px;color:var(--white);font-weight:700;margin-top:2px}
.intake p{font-size:10px;color:#e6f0e0;margin:6px 0 8px}
.field{height:22px;background:#2a2a2a;color:#aaa;font-size:10px;line-height:22px;padding-left:7px;margin-bottom:8px;border-radius:2px;font-family:"Arimo",sans-serif}
.field.message{height:60px;background:#e6e6e6;color:#888;line-height:20px}
.submit{position:absolute;left:128px;bottom:0;width:55px;height:21px;background:#000;color:var(--white);font-size:10px;text-align:center;line-height:21px;border-radius:3px 3px 0 0}
.intro{position:absolute;left:334px;top:505px;width:560px;font-size:10.5px;line-height:18.5px;color:#444}
.intro h2{font-size:14px;color:var(--ink);font-weight:700;line-height:20px}
.intro p{margin-bottom:18px}
.cards{position:absolute;left:112px;top:811px;width:787px;height:207px}
.card{position:absolute;top:0;width:253px;height:207px;overflow:hidden;border-radius:6px;background:linear-gradient(90deg,#d6d6d6 0%,#f4f4f4 45%,#fff 100%);box-shadow:0 4px 6px rgba(0,0,0,.3);padding:16px 16px 0 17px}
.card h3{font-family:"PT Sans",sans-serif;font-weight:400;font-size:23px;color:#333;line-height:26px;margin-left:4px;white-space:nowrap}
.card h3.long{font-size:20.5px;margin-left:0;letter-spacing:-.1px}
.card-photo{width:212px;height:52px;margin:8px 0 6px 3px}
.card p{font-family:"Arimo",sans-serif;font-size:10px;line-height:13.5px;color:#111;text-align:justify}
.card .more{display:block;text-align:right;font-weight:700;font-size:10px;margin-top:1px;color:#111}
.footer{position:absolute;left:97px;top:1056px;width:817px;height:121px;background:linear-gradient(180deg,#a10b18 0%,#8c0812 60%,var(--red-dark) 100%);color:var(--white);font-family:"Arimo",sans-serif;font-size:9.6px;line-height:15.3px;padding:14px 19px}
.footer-links{margin-bottom:16px}
.footer-links span{margin-right:10px}
.disclaimer{width:570px}
.badge{position:absolute;right:19px;top:23px;width:87px;height:70px;background:var(--white);box-shadow:8px 8px 0 rgba(255,255,255,.25)}
.badge i{position:absolute;left:10px;top:10px;width:36px;height:50px;background:#4f86c6}
</style>
</head>
<body>
<div class="canvas">
  <div class="page"></div>

  <header class="header">
    <div class="brand">
      <span class="brand-mark"></span>
      <div class="brand-name"><small>Law Office of</small>Marta K. Dolvenidze</div>
    </div>
    <div class="phone">
      <svg viewBox="0 0 22 22" aria-hidden="true"><rect width="22" height="22" rx="4" fill="#fff"/><path d="M7 4c1 0 2 2.5 2 3.3 0 .8-1.3 1.2-1.3 2 0 1.4 3.6 5 5 5 .8 0 1.2-1.3 2-1.3s3.3 1 3.3 2c0 1.3-1.6 3-3 3C9.7 18 4 12.3 4 7c0-1.4 1.7-3 3-3z" fill="#7a0710"/></svg>
      415-555-0187
    </div>
  </header>

  <nav class="nav">
    <a class="current" href="#">HOME</a>
    <a href="#">ABOUT US</a>
    <a href="#">AREAS OF PRACTICE</a>
    <a href="#">RESOURCES</a>
    <a href="#">BLOG</a>
    <a href="#">FAQ</a>
    <a href="#">CONTACT US</a>
  </nav>
  <span class="nav-fold left"></span>
  <span class="nav-fold right"></span>

  <section class="hero" role="img" aria-label="Photo of a large tree on green grass at sunset">
    <div class="hero-line">Always Protecting Our Client's Interests!</div>
  </section>

  <aside class="intake">
    <h3>Free Consultation</h3>
    <p>Fields marked with * are required.</p>
    <div class="field">Name *</div>
    <div class="field">Email *</div>
    <div class="field">Phone</div>
    <div class="field">Subject *</div>
    <div class="field message">Message *</div>
    <div class="submit">SUBMIT</div>
  </aside>

  <section class="intro">
    <h2>Welcome to Debt Help 411 - Complete Bankruptcy Information</h2>
    <p>The Law Office of Marta K. Dolvenidze is a consumer law office dedicated to consumer protection and zealously defending the rights of our clients. We offer the big firm quality legal representation with a small firm individualized attention to each client.</p>
    <p>Our office offers services in: all types of consumer bankruptcy filings, i.e. Chapter 7, Chapter 13, Chapter 11, negotiating a settlement of your debts, assisting you in the defense of collection litigation and defending you against foreclosure. Please review our site and see what we may be able to offer you. Feel free to call us at (415) 555-0187 to use our free consultation.</p>
    <h2>Speak to a Lawyer</h2>
    <p>Unlike some other law firms, when you call the Law Office of Marta K. Dolvenidze you will speak to an actual attorney. Not a paralegal or assistant. And even after retaining our office you will still speak to an attorney unlike other firms where you cannot get a hold of your attorney after several attempts.</p>
  </section>

  <section class="cards">
    <article class="card" style="left:0">
      <h3>Debt Relief</h3>
      <div class="card-photo" role="img" aria-label="Photo of a lawyer meeting with a couple" style="background:linear-gradient(90deg,#3c3a40,#8a7f78 45%,#d9d2c8 75%,#9a8b80)"></div>
      <p>This page is available, however, but because occasionally circumstances occur in which toil and pain can procure him some great. To take a trivial example, which of us ever undertakes laborious physical exercise, except to obtain some advantage from it.</p>
      <span class="more">read more...</span>
    </article>
    <article class="card" style="left:267px">
      <h3 class="long">Foreclosure Prevention</h3>
      <div class="card-photo" role="img" aria-label="Photo of a smiling family in a car" style="background:linear-gradient(90deg,#2e2e2e,#8c7866 35%,#c9b9a6 60%,#5c5c5c)"></div>
      <p>This page is available, however, but because occasionally circumstances occur in which toil and pain can procure him some great. To take a trivial example, which of us ever undertakes laborious physical exercise, except to obtain some advantage from it.</p>
      <span class="more">read more...</span>
    </article>
    <article class="card" style="left:533px">
      <h3>Chapter 13</h3>
      <div class="card-photo" role="img" aria-label="Photo of a relaxed couple at home" style="background:linear-gradient(90deg,#cfd8e2,#b89a84 40%,#8e7563 65%,#dfe6ee)"></div>
      <p>This page is available, however, but because occasionally circumstances occur in which toil and pain can procure him some great. To take a trivial example, which of us ever undertakes laborious physical exercise, except to obtain some advantage from it.</p>
      <span class="more">read more...</span>
    </article>
  </section>

  <footer class="footer">
    <div class="footer-links"><span>Go to top</span> Copyright © 2010 KDLaw. All Rights Reserved. | Web Development by Webtrellis | Design by Norvik</div>
    <p class="disclaimer">Disclaimer: The Law Offices of Marta K. Dolvenidze is a Debt Relief law firm as defined by 11 U.S.C. 528. We help people file for Bankruptcy Relief under the Bankruptcy Code. The information contained on this website is not to be construed as legal advice. It is not intended to solicit or form an attorney-client relationship. We do not guarantee any result and prior results do not guarantee a similar outcome. This is an attorney advertisement and this website is for informational purposes only.</p>
    <div class="badge" role="img" aria-label="Professional association membership badge"><i></i></div>
  </footer>
</div>
</body>
</html>
```